Web Design Project - Brightvaultly.com.au

We need a redesign for one of our masthead finance properties, brightvaultly.com.au. The new site will feature easy to use tools (calculator etc.) and comparison tables, with an emphasis on sharp, consise content and less clutter.
The redesign should reflect this new approach by appearing clean, polished and professional.
Example Sites for new look and feel:
http://www.pennoria.com.au/savings-accounts
http://kelbu.com.au/savings-accounts/
I've attached a very basic wireframe. Details on different elements as follows:
Find an Account Tool -
Basic redesign of exisiting tool on brightvaultly.com.au
Comparsion Table -
To run the size roughly outlined in wireframe, fields to include: Company
Product
Maximum Rate
Interest Earned
Go To Site
Footer -
To include the links currently shown on brightvaultly.com.au as well as additional links for 'Banks savings accounts', 'High interest accounts', 'online accounts', 'Interest Rates', 'Saving money tips'
Logo
Please include a logo mock up
Modules -
Should include Image 120x60, headline, short description

```html
<!DOCTYPE html>
<html lang="en">
<head>
<meta charset="utf-8">
<title>Brightvaultly.com.au – Savings Accounts</title>
<link rel="stylesheet" href="https://fonts.googleapis.com/css2?family=PT+Sans:wght@400;700&display=swap">
<style>
:root{
  --ink:#3a3d40;
  --muted:#7a7e82;
  --header:#2b2e31;
  --header-2:#3b3f43;
  --green:#7ab52c;
  --green-light:#a6d04e;
  --green-dark:#4f7d17;
  --blue:#1f5e8e;
  --blue-light:#d6e8f5;
  --orange:#e2701f;
  --hero:#e9ecee;
  --line:#d9dde0;
  --footer:#2c3328;
  --footer-2:#232821;
  --white:#ffffff;
}
*{box-sizing:border-box;margin:0;padding:0}
html,body{width:738px;height:1200px;overflow:hidden}
body{font-family:"PT Sans",Arial,sans-serif;color:var(--ink);background:var(--white);position:relative;font-size:11px}
.abs{position:absolute}

.site-header{left:0;top:0;width:738px;height:72px;background:linear-gradient(var(--header-2),var(--header))}
.brand{left:22px;top:18px;display:flex;align-items:center;gap:8px}
.brand-mark{width:32px;height:32px;border-radius:50%;background:var(--green-light)}
.brand-name{font-size:22px;font-weight:700;color:var(--white);line-height:1}
.util-links{right:22px;top:4px;color:#c9ccce;font-size:8px}
.header-ad{left:470px;top:16px;width:180px;height:46px;background:var(--white);border-radius:2px;display:flex;align-items:center;justify-content:center;gap:6px}
.header-ad .sq{width:12px;height:12px;background:var(--green)}
.header-ad span{font-size:13px;font-weight:700;color:var(--blue)}
.ad-label{left:655px;top:52px;color:#9a9da0;font-size:7px}

.main-nav{left:0;top:72px;width:738px;height:28px;background:linear-gradient(var(--green-light),var(--green));display:flex;align-items:center;padding-left:34px}
.main-nav a{color:var(--white);text-decoration:none;font-size:11px;font-weight:700;padding:0 10px;line-height:28px}
.main-nav a.active{background:var(--green-dark)}
.nav-cta{right:22px;top:76px;height:20px;padding:0 10px;background:var(--white);color:var(--green-dark);font-weight:700;font-size:10px;line-height:20px;border-radius:2px}

.hero{left:0;top:100px;width:738px;height:222px;background:radial-gradient(ellipse at 30% 60%,#fbfcfc,var(--hero) 70%)}
.hero-art{left:30px;top:115px;width:300px;height:195px;border-radius:6px;background:radial-gradient(circle at 70% 60%,#f3b8c6,#d9dfe4 55%,var(--hero) 80%)}
.finder{left:360px;top:112px;width:340px}
.finder h1{font-size:28px;color:var(--ink);font-weight:700;line-height:1}
.finder .lead{color:var(--green);font-size:10px;margin:4px 0 10px}
.field-label{font-size:10px;font-weight:700;margin:4px 0 2px}
.field{width:215px;height:20px;background:var(--white);border:1px solid #c7cbce;border-radius:2px;position:relative}
.field.select::after{content:"";position:absolute;right:6px;top:7px;border:4px solid transparent;border-top-color:var(--muted)}
.find-row{display:flex;align-items:center;gap:22px;margin-top:12px}
.btn-find{width:105px;height:28px;background:linear-gradient(var(--green-light),var(--green));color:var(--white);font-weight:700;font-size:14px;text-align:center;line-height:28px;border-radius:3px}
.more-options{font-size:9px;color:var(--blue);text-decoration:underline}

.compare{left:38px;top:338px;width:380px}
.compare-head{height:28px;background:linear-gradient(#3b86c0,var(--blue));color:var(--white);display:flex;align-items:center;justify-content:center;gap:14px}
.compare-head strong{font-size:14px}
.compare-head span{font-size:8px;opacity:.85}
.compare table{width:100%;border-collapse:collapse;font-size:8px}
.compare th{background:var(--blue-light);color:var(--blue);font-size:8px;text-align:left;padding:5px 4px;text-transform:uppercase}
.compare td{padding:0 4px;height:40px;border-bottom:1px solid var(--line)}
.compare tr.featured td{background:#fff6ee;border-top:2px solid var(--orange);border-bottom:2px solid var(--orange)}
.co{font-weight:700;color:var(--blue)}
.rate{font-weight:700;font-size:10px}
.prod{color:var(--ink)}
.go{display:inline-block;background:var(--green-dark);color:var(--white);font-size:7px;padding:3px 7px;border-radius:2px;font-weight:700}
.more-info{left:38px;top:812px;font-size:8px;color:var(--blue)}

.side-ad{left:440px;top:345px;width:258px;height:190px;border:1px solid var(--line);display:flex;flex-direction:column;align-items:center;justify-content:center;gap:8px}
.side-ad .name{font-size:22px;font-weight:700;color:var(--blue)}
.side-ad .go{background:var(--green);font-size:8px;padding:4px 10px}
.sponsor-title{left:440px;top:548px;width:258px;height:20px;background:var(--header);color:var(--white);font-weight:700;font-size:10px;line-height:20px;padding-left:8px}
.module{left:440px;width:258px;display:flex;gap:8px}
.module .logo{width:78px;height:52px;background:var(--blue-light);display:flex;align-items:center;justify-content:center;font-size:9px;font-weight:700;color:var(--blue);flex:none;text-align:center}
.module h3{font-size:9px;color:var(--blue)}
.module p{font-size:8px;color:var(--muted);line-height:1.3}

.welcome{left:38px;top:835px;width:380px}
.welcome h2{font-size:20px;color:var(--blue)}
.welcome .intro{color:var(--orange);font-size:10px;margin:6px 0;line-height:1.35}
.welcome p{font-size:9px;color:var(--muted);line-height:1.4}
.piggy-art{left:440px;top:860px;width:90px;height:90px;border-radius:50%;background:radial-gradient(circle at 40% 40%,#a9dcf3,#5bb4dd)}

.site-footer{left:0;top:1030px;width:738px;height:154px;background:var(--footer)}
.footer-col h4{color:var(--green-light);font-size:14px;margin-bottom:6px}
.footer-col ul{list-style:none}
.footer-col li{color:#cfd3cc;font-size:8px;line-height:15px}
.footer-col li::before{content:"» ";color:var(--green-light)}
.links-1{left:34px;top:1042px}
.links-2{left:160px;top:1063px}
.social{left:300px;top:1042px;width:130px}
.social h4{color:#d7dbd3;font-size:18px;font-weight:700;line-height:1}
.social-icons{display:flex;gap:6px;margin-top:12px}
.social-icons span{width:18px;height:18px;background:#5a6452;border-radius:3px}
.articles{left:470px;top:1042px;width:240px}
.articles h5{color:var(--green-light);font-size:9px;margin-top:4px}
.articles p{color:#aeb3aa;font-size:8px;line-height:1.3}
.articles .read{color:var(--green-light);font-size:8px;margin-top:6px}
.copyright{left:0;top:1184px;width:738px;height:16px;background:var(--footer-2);color:#9ea39a;font-size:7px;line-height:16px;padding-left:34px}
</style>
</head>
<body>

<header class="abs site-header"></header>
<div class="abs brand"><span class="brand-mark"></span><span class="brand-name">Brightvaultly</span></div>
<div class="abs util-links">Login | Signup | Help</div>
<div class="abs header-ad"><span class="sq"></span><span>Tallow Home Loans</span></div>
<div class="abs ad-label">Advertisement</div>

<nav class="abs main-nav">
  <a href="#">Home</a><a href="#" class="active">Compare</a><a href="#">Guide</a><a href="#">Calculator</a><a href="#">High interest</a>
</nav>
<div class="abs nav-cta">Great Articles</div>

<section class="abs hero"></section>
<div class="abs hero-art" role="img" aria-label="Illustration of a pink piggy bank under a magnifying glass"></div>
<div class="abs finder">
  <h1>Find an Account Tool</h1>
  <p class="lead">Need some help? Use our Savings Account tool</p>
  <div class="field-label">Deposit Amount</div><div class="field"></div>
  <div class="field-label">Savings Duration</div><div class="field select"></div>
  <div class="field-label">Account Type</div><div class="field select"></div>
  <div class="find-row"><div class="btn-find">Find Account</div><span class="more-options">More Search Options</span></div>
</div>

<section class="abs compare">
  <div class="compare-head"><strong>Comparison Table</strong><span>Rates updated 16 July 2012</span></div>
  <table>
    <thead><tr><th>Company</th><th>Product</th><th>Maximum Rate</th><th>Interest Earned</th><th>Go to Site</th></tr></thead>
    <tbody>
      <tr><td class="co">Orvane Direct</td><td class="prod">Savings Saver</td><td class="rate">5.70%</td><td>$23.96<br>No end date</td><td><span class="go">VIEW NOW</span></td></tr>
      <tr class="featured"><td class="co">Tallow</td><td class="prod">Rate Saver</td><td class="rate">5.70%</td><td>$23.96<br>No end date</td><td><span class="go">VIEW NOW</span></td></tr>
      <tr><td class="co">Lumo Bank</td><td class="prod">Bonus Saver</td><td class="rate">5.70%</td><td>$23.96<br>No end date</td><td><span class="go">VIEW NOW</span></td></tr>
      <tr><td class="co">Greatfield</td><td class="prod">Builder Saver Account</td><td class="rate">5.70%</td><td>$23.96<br>No end date</td><td><span class="go">VIEW NOW</span></td></tr>
      <tr><td class="co">Civara Bank</td><td class="prod">Online Saver</td><td class="rate">5.70%</td><td>$23.96<br>No end date</td><td><span class="go">VIEW NOW</span></td></tr>
      <tr><td class="co">Nordale Bank</td><td class="prod">Smart Saver</td><td class="rate">5.70%</td><td>$23.96<br>No end date</td><td><span class="go">VIEW NOW</span></td></tr>
      <tr><td class="co">St Merrin</td><td class="prod">Incentive Saver</td><td class="rate">5.70%</td><td>$23.96<br>No end date</td><td><span class="go">VIEW NOW</span></td></tr>
      <tr><td class="co">Orvane</td><td class="prod">Savings Saver</td><td class="rate">5.70%</td><td>$23.96<br>No end date</td><td><span class="go">VIEW NOW</span></td></tr>
      <tr><td class="co">Calder Union</td><td class="prod">Online Saver</td><td class="rate">5.70%</td><td>$23.96<br>No end date</td><td><span class="go">VIEW NOW</span></td></tr>
      <tr><td class="co">Lumo Bank</td><td class="prod">Holiday Saver</td><td class="rate">5.70%</td><td>$23.96<br>No end date</td><td><span class="go">VIEW NOW</span></td></tr>
    </tbody>
  </table>
</section>
<div class="abs more-info">Click for More Info</div>

<aside class="abs side-ad"><span class="name">Tallow Home Loans</span><span class="go">FIND OUT MORE</span></aside>
<div class="abs sponsor-title">Sponsor Links</div>
<div class="abs module" style="top:578px"><div class="logo">Tallow</div><div><h3>Home loans made simple</h3><p>Compare our variable and fixed rate loans online today. Low fees, flexible repayments and friendly local support.</p></div></div>
<div class="abs module" style="top:660px"><div class="logo">Anvara</div><div><h3>Online saver account</h3><p>Earn a bonus rate on your savings each month you deposit. No account keeping fees and easy online access.</p></div></div>
<div class="abs module" style="top:742px"><div class="logo">Lumo Bank</div><div><h3>High interest savings</h3><p>Grow your balance with a competitive ongoing rate. Open an account in minutes with nothing to pay.</p></div></div>

<section class="abs welcome">
  <h2>Welcome to Savings Accounts</h2>
  <p class="intro">Our savings account guide helps you compare rates from trusted lenders, so your money works harder every single month.</p>
  <p>Whether you are saving for a home, a holiday or a rainy day fund, the right account matters. Use our tools to sort accounts by rate, fees and access, then read our guides to learn how interest is paid and how bonus conditions work. Clear facts, fewer surprises and a smarter way to save.</p>
</section>
<div class="abs piggy-art" role="img" aria-label="Illustration of a blue piggy bank with coins"></div>

<footer class="abs site-footer"></footer>
<div class="abs footer-col links-1"><h4>Useful Links</h4><ul><li>Home</li><li>Compare</li><li>Guide</li><li>Calculator</li><li>High interest</li></ul></div>
<div class="abs footer-col links-2"><ul><li>Banks savings accounts</li><li>High interest accounts</li><li>Online accounts</li><li>Interest Rates</li><li>Saving money tips</li></ul></div>
<div class="abs social"><h4>Social<br>share</h4><div class="social-icons"><span></span><span></span><span></span><span></span></div></div>
<div class="abs footer-col articles">
  <h4>Saving A/c Articles</h4>
  <h5>Fund Home Saving Accounts</h5>
  <p>Simple steps to plan a deposit and stay on track.</p>
  <h5>Teaching Children How to Save</h5>
  <p>Fun ideas to build good money habits early.</p>
  <div class="read">Read All Articles</div>
</div>
<div class="abs copyright">© 2012 All Rights Reserved. Copyright brightvaultly.com.au, Privacy Policy, Terms of Use</div>

</body>
</html>
```